New Webpage for High Class Expert Witness Services Company

We are looking for a minimalist design for a webpage that just has our logo and an entry form offer to connect with one of our Liaisons.
The entry form should just ask for Name, Email, Contact Info and Description of Project.

Company Name is: The Marlowe Crest Advisory Services

Number of Pages Required

1 page

```html
<!DOCTYPE html>
<html lang="en">
<head>
<meta charset="utf-8">
<title>The Marlowe Crest Advisory Services – Contact</title>
<link rel="stylesheet" href="https://fonts.googleapis.com/css2?family=Roboto:wght@300;400;500;700;900&family=Inter:wght@400;500&display=swap">
<style>
:root{
  --page:#ffffff;
  --navy-deep:#0e141d;
  --navy-mid:#1b2a3a;
  --navy-glow:#2a4258;
  --slate-dark:#2f2f31;
  --slate-mid:#48464a;
  --olive:#3b3a33;
  --card-top:#b3b3b6;
  --card-bottom:#8a8b8f;
  --field:#ffffff;
  --ink:#111111;
  --ink-soft:#222222;
  --light:#ffffff;
  --logo-ink:#d6d6d8;
  --accent:#f7941d;
}
*{box-sizing:border-box;margin:0;padding:0}
html,body{width:1096px;height:1200px;overflow:hidden;background:var(--page)}
body{position:relative;font-family:"Inter",sans-serif}

.screen{position:absolute;left:77px;width:940px;height:496px;overflow:hidden}
.screen--hero{top:72px}
.screen--centered{top:617px}

.backdrop{position:absolute;inset:0}
.screen--hero .backdrop{
  background:
    radial-gradient(ellipse at 42% 45%, var(--navy-glow) 0%, rgba(42,66,88,0) 45%),
    radial-gradient(ellipse at 18% 30%, #223447 0%, rgba(34,52,71,0) 40%),
    linear-gradient(100deg, var(--navy-mid) 0%, #172230 50%, var(--navy-deep) 100%);
}
.screen--centered .backdrop{
  background:
    radial-gradient(ellipse at 80% 55%, var(--olive) 0%, rgba(59,58,51,0) 55%),
    linear-gradient(90deg, var(--slate-mid) 0%, var(--slate-dark) 45%, #333230 100%);
}

.brand{position:absolute;font-family:"Roboto",sans-serif;font-weight:500;color:var(--logo-ink);
  font-size:22px;line-height:25px;letter-spacing:2.5px;text-transform:uppercase}
.screen--hero .brand{left:120px;top:36px}
.screen--centered .brand{left:0;right:0;top:34px;text-align:center}

.headline{position:absolute;left:117px;top:242px;font-family:"Roboto",sans-serif;font-weight:700;
  color:var(--light);font-size:43px;line-height:48px;width:420px}
.tagline{position:absolute;left:121px;top:354px;font-family:"Roboto",sans-serif;color:var(--light);
  font-size:22px;line-height:31px}
.tagline strong{display:block;font-weight:700}
.tagline span{display:block;font-weight:300}

.copyright{position:absolute;left:0;right:0;top:464px;text-align:center;color:var(--light);
  font-family:"Inter",sans-serif;font-size:10px}

.contact-card{position:absolute;border-radius:12px;
  background:linear-gradient(180deg,var(--card-top) 0%,var(--card-bottom) 100%)}
.screen--hero .contact-card{left:521px;top:36px;width:302px;height:402px}
.screen--centered .contact-card{left:244px;top:117px;width:452px;height:326px}

.card-title{position:absolute;font-family:"Roboto",sans-serif;font-weight:700;color:var(--ink);font-size:22px;line-height:26px}
.screen--hero .card-title{left:28px;top:15px}
.screen--centered .card-title{left:0;right:0;top:19px;text-align:center}
.card-intro{position:absolute;left:30px;top:46px;width:230px;font-size:11.5px;line-height:15px;color:var(--ink-soft)}

.field{position:absolute;background:var(--field);border-radius:17px;font-size:9.5px;color:var(--ink-soft);
  padding:0 16px;display:flex;align-items:center}
.field--area{align-items:flex-start;padding-top:11px;border-radius:17px}
.screen--hero .field{left:22px;width:267px;height:34px}
.screen--centered .field{left:31px;width:386px;height:34px}
.screen--hero .f-name{top:93px}
.screen--hero .f-email{top:132px}
.screen--hero .f-contact{top:172px}
.screen--hero .f-desc{top:211px;height:108px}
.screen--centered .f-name{top:65px}
.screen--centered .f-email{top:104px}
.screen--centered .f-contact{top:143px}
.screen--centered .f-desc{top:183px;height:70px}

.submit{position:absolute;height:41px;border-radius:20px;background:var(--accent);color:var(--light);
  font-family:"Roboto",sans-serif;font-weight:700;font-size:18px;display:flex;align-items:center;justify-content:center;
  box-shadow:0 3px 6px rgba(0,0,0,.25)}
.screen--hero .submit{left:22px;top:332px;width:267px}
.screen--centered .submit{left:31px;top:263px;width:386px}
</style>
</head>
<body>

<section class="screen screen--hero">
  <div class="backdrop" role="img" aria-label="Dark blue digital background with a glowing medical shield and cross icons"></div>
  <div class="brand">Marlowe Crest<br>Advisory Services</div>
  <h1 class="headline">The Marlowe Crest Advisory Services</h1>
  <p class="tagline"><strong>High Class Expert Witness</strong><span>Services Company</span></p>
  <div class="contact-card">
    <h2 class="card-title">Contact Us</h2>
    <p class="card-intro">Lorem ipsum dolor sit amet consectetur adipiscing elit</p>
    <div class="field f-name">Name</div>
    <div class="field f-email">Email</div>
    <div class="field f-contact">Contact Info</div>
    <div class="field field--area f-desc">Description of Project</div>
    <div class="submit">SUBMIT</div>
  </div>
  <p class="copyright">Copyright © 2026 All Rights Reserved</p>
</section>

<section class="screen screen--centered">
  <div class="backdrop" role="img" aria-label="Dimmed photo of a doctor with a stethoscope attending a soldier"></div>
  <div class="brand">Marlowe Crest<br>Advisory Services</div>
  <div class="contact-card">
    <h2 class="card-title">The Marlowe Crest Advisory Services</h2>
    <div class="field f-name">Name</div>
    <div class="field f-email">Email</div>
    <div class="field f-contact">Contact Info</div>
    <div class="field field--area f-desc">Description of Project</div>
    <div class="submit">SUBMIT</div>
  </div>
  <p class="copyright">Copyright © 2026 All Rights Reserved</p>
</section>

</body>
</html>
```